Business Card Design Project

Looking for a logo and business card for a Real State Business i will be opening. The name is not choosen yet , but will probably be RWT IMOVEIS.
I was thinking black and silver colors, but am open to nice ideas.
I did add a business card that i liked a lot, am looking for something like that, with logo in black or silver in a black card. The logo i was thinking in the letters RWT as i uploaded or something or little and cute buildings or a house...just ideas, can be any nice logo.
Updates

You guys can add other colors if you want, I like colors very "BRIGHT" and "open", like red, pink, strong colors. almost glow in the dark colors. lol

Designers,

I've increased more 88 dollars in the budget for 1st place cause I will want envelope designs... small and big sizes.

So 1st place is now U$248,00. 

No need to send the envelope designs right now... only the business cards designs.

Thank you.

Industry/Entity Type

Business

Requirements
Must have
• Marcela Tavares Rocha

www.RWTimoveis-exemplo.com.br

+554187316042

marcela@rwtimoveis-exemplo.com.br

```html
<!DOCTYPE html>
<html lang="pt-BR">
<head>
<meta charset="utf-8">
<title>RWT IMOVEIS — Cartão de visita e papelaria</title>
<link href="https://fonts.googleapis.com/css2?family=Michroma&display=swap" rel="stylesheet">
<style>
  :root {
    --board-light: #3c3c3c;
    --board-dark: #0a0a0a;
    --paper: #121212;
    --paper-edge: #1a1a1a;
    --ink: #f2f2f2;
    --ink-soft: #c9c9c9;
    --mark-faint: #1c1c1c;
  }
  * { margin: 0; padding: 0; box-sizing: border-box; }
  html, body { width: 1200px; height: 900px; overflow: hidden; }
  body {
    position: relative;
    font-family: "Michroma", sans-serif;
    color: var(--ink);
    background: radial-gradient(ellipse 700px 520px at 840px 360px, var(--board-light) 0%, #222 45%, var(--board-dark) 100%);
  }
  .label {
    position: absolute;
    font-size: 14px;
    letter-spacing: 1.5px;
    color: var(--ink);
    line-height: 1;
  }
  .sheet {
    position: absolute;
    background: var(--paper);
    box-shadow: 0 0 0 1px var(--paper-edge), 0 6px 18px rgba(0,0,0,.55);
  }
  .card-back { left: 72px; top: 58px; width: 344px; height: 484px; overflow: hidden; }
  .card-front { left: 441px; top: 58px; width: 344px; height: 484px; }
  .envelope { left: 192px; top: 628px; width: 461px; height: 229px; }
  .envelope-open { position: absolute; left: 697px; top: 554px; width: 460px; height: 301px; }
  .envelope-open svg { display: block; filter: drop-shadow(0 6px 12px rgba(0,0,0,.55)); }

  .faint-mark {
    position: absolute;
    left: 0; top: 160px;
    width: 320px; height: 324px;
    background: radial-gradient(ellipse 220px 240px at 110px 200px, var(--mark-faint) 0%, var(--paper) 100%);
  }

  .contact {
    position: absolute;
    font-style: normal;
    text-align: right;
    color: var(--ink-soft);
    line-height: 1.3;
    letter-spacing: .3px;
    white-space: nowrap;
  }
  .contact .gap { display: block; height: 0.8em; }
  .contact .person { color: var(--ink); }
  .card-back .contact { right: 40px; top: 384px; font-size: 7.2px; }
  .envelope .contact { right: 37px; top: 150px; font-size: 6px; }
  .envelope-open .contact { right: 37px; top: 224px; font-size: 6px; }

  .brand {
    position: absolute;
    display: flex;
    align-items: center;
    gap: 8px;
    font-size: 15px;
    letter-spacing: .8px;
    color: var(--ink);
    white-space: nowrap;
  }
  .brand .brand-square { width: 10px; height: 10px; background: var(--ink); }
  .envelope .brand { left: 40px; top: 68px; }
  .envelope-open .brand { left: 40px; top: 144px; }

  .card-front .brand-vertical {
    position: absolute;
    left: 279px; top: 245px;
    transform: translate(-50%, -50%) rotate(-90deg);
    font-size: 24px;
    letter-spacing: 1px;
    gap: 14px;
  }
  .card-front .brand-vertical .brand-square { width: 14px; height: 14px; }
</style>
</head>
<body>
  <span class="label" style="left:92px; top:38px;">BACK</span>
  <span class="label" style="left:459px; top:38px;">FRONT</span>
  <span class="label" style="left:529px; top:608px;">ENVELOPE</span>
  <span class="label" style="left:947px; top:534px;">ENVELOPE OPEN</span>

  <section class="sheet card-back">
    <div class="faint-mark" role="img" aria-label="Large faint brand decoration in dark grey"></div>
    <address class="contact">
      <span class="person">Marcela Tavares Rocha</span>
      <span class="gap"></span>
      Av. das Araucárias, 1520<br>
      CEP 80420-310<br>
      Campo Alto-PR
      <span class="gap"></span>
      +554187316042<br>
      marcela@rwtimoveis-exemplo.com.br<br>
      www.RWTimoveis-exemplo.com.br
    </address>
  </section>

  <section class="sheet card-front">
    <div class="brand brand-vertical">
      <span class="brand-square"></span>
      <span class="brand-name">RWT IMOVEIS</span>
    </div>
  </section>

  <section class="sheet envelope">
    <div class="brand">
      <span class="brand-square"></span>
      <span class="brand-name">RWT IMOVEIS</span>
    </div>
    <address class="contact">
      Av. das Araucárias, 1520<br>
      CEP 80420-310<br>
      Campo Alto-PR
      <span class="gap"></span>
      +554187316042<br>
      marcela@rwtimoveis-exemplo.com.br<br>
      www.RWTimoveis-exemplo.com.br
    </address>
  </section>

  <section class="envelope-open">
    <svg width="460" height="301" viewBox="0 0 460 301" aria-hidden="true">
      <polygon points="0,56 26,0 460,0 460,301 0,301" fill="#121212" stroke="#1a1a1a" stroke-width="1"/>
    </svg>
    <div class="brand">
      <span class="brand-square"></span>
      <span class="brand-name">RWT IMOVEIS</span>
    </div>
    <address class="contact">
      Av. das Araucárias, 1520<br>
      CEP 80420-310<br>
      Campo Alto-PR
      <span class="gap"></span>
      +554187316042<br>
      marcela@rwtimoveis-exemplo.com.br<br>
      www.RWTimoveis-exemplo.com.br
    </address>
  </section>
</body>
</html>
```